Flyer-Design für Prozessfinanzierungsfirma
Zielgruppe
Wir sind eine Prozessfinanzierungsfirma. im Versicherungsbereich die größte Österreichs mit mehr als 50.000 Klienten und unser neues Projekt ist die Prozessfinanzierung von Patienten die durch einen Kunstfehler (Fehler von Ärzten) auf Schadenersatz klagen wollen aber nicht die Finanziellen Möglichkeiten haben.
Aufgabenstellung
Folder soll eine DIN A4 Doppelseite sein (also 4 A4 Seiten)
plus extra ein A4 Einlage Blatt Fragebogen fix vorgegebene Fragen.
#258971 Dieser Folder ist für die gleiche Firma im Bereich Versicherungen
www.heilirrtum-hilfe.at. TEXTE und DESIGN - FARBEN und INHALTE von dieser Homepage übernehmen
die Seite www.tarifquelle.at ist die gleiche Prozessfinanzierungsfirma - hier gibt es bereits einen Folder. Ich lade diesen hoch...
Diese Fragen sind unbedingt 1:1 zu übernehmen für das Einlageblatt :
o Was waren meine Erkrankungen vor der Behandlung, inkl. Dauermedikation?
o Warum ging ich zum Arzt?
o Was hat mir der Arzt empfohlen?
o Wurde ich über die unterschiedlichen Behandlungsmöglichkeiten aufgeklärt?
o Was wollte ich haben?
o Was wurde gemacht?
o Was hat der Arzt aus meiner Sicht falsch gemacht?
o Was wurde als weiterer Behandlungsweg empfohlen?
o Habe ich den Arzt mit meinem Problem konfrontiert?
o Wie hat mein Arzt darauf reagiert?
o Was ist jetzt genau schlechter als vorher?
Bei dem A4 Einlageblatt sollen auf der Vorderseite und der halben Rückseite diese Fragen mit entsprechendem Platz für den Text zum ausfüllen erscheinen und die untere Hälfte der 2. Seite mit einem kurzen Slogan nochmal auf unsere Leistung aufmerksam machen - ein Feld in Kreditkartengrösse für den Empfehlungsbgeber weiss zum einkleben einer Karte freibleiben und die Firmendaten (siehe Homepage) mit Anschrift, Telefonnummer und e-mailadresse angegeben sein

```html
<!DOCTYPE html>
<html lang="de">
<head>
<meta charset="utf-8">
<title>Kunstfehler – Prozessfinanzierung</title>
<link href="https://fonts.googleapis.com/css2?family=Roboto:wght@300;700&family=Roboto+Condensed:ital,wght@1,400&family=Source+Sans+3:ital,wght@0,400;0,600;0,700;1,700&family=Libre+Baskerville:ital@1&display=swap" rel="stylesheet">
<style>
  :root {
    --wine: #7a1520;
    --ink: #1a1a1a;
    --paper: #ffffff;
    --paper-grey: #e4e4e4;
    --quote-bar: #c8c8c8;
  }
  * { margin: 0; padding: 0; box-sizing: border-box; }
  html, body { width: 1200px; height: 849px; overflow: hidden; }
  body { position: relative; font-family: "Source Sans 3", sans-serif; color: var(--ink); }

  .page { position: absolute; top: 0; width: 600px; height: 849px; overflow: hidden; }
  .page--left { left: 0; background: var(--paper); }
  .page--right { left: 600px; background: var(--paper-grey); }

  .running-head { position: absolute; top: 33px; font-family: "Roboto Condensed", sans-serif; font-style: italic; font-size: 12.5px; letter-spacing: 0.2px; }
  .running-bar { position: absolute; top: 37px; height: 8px; width: 437px; background: var(--wine); border-radius: 3px; }

  .page-title { position: absolute; top: 66px; font-family: "Roboto", sans-serif; font-weight: 700; font-size: 24px; letter-spacing: 0.1px; }

  .lead-quote { position: absolute; left: 36px; top: 107px; width: 528px; height: 53px; }
  .lead-quote::before { content: ""; position: absolute; left: 0; top: 0; width: 9px; height: 53px; background: var(--quote-bar); border-radius: 3px; }
  .lead-quote p { position: absolute; left: 21px; top: 12px; width: 500px; font-family: "Libre Baskerville", serif; font-style: italic; font-size: 11px; line-height: 14.5px; letter-spacing: 0.9px; }

  .column { position: absolute; font-size: 10px; line-height: 12.1px; text-align: justify; hyphens: auto; }
  .column p { margin-bottom: 12.1px; }
  .column h3 { font-size: 9.5px; font-weight: 700; letter-spacing: 0.3px; line-height: 12.1px; margin-bottom: 12.1px; text-align: justify; }
  .accent { color: var(--wine); font-weight: 600; }
  .accent-strong { color: var(--wine); font-weight: 700; }
  .signature { font-weight: 700; font-style: italic; }
  .bullets { list-style: none; margin-bottom: 12.1px; }
  .bullets li { padding-left: 5px; text-indent: -5px; }
  .bullets li::before { content: "• "; }
  .bullets--indented li { padding-left: 6px; text-indent: -6px; }

  .photo { position: absolute; left: 0; top: 518px; width: 600px; height: 331px;
    background: linear-gradient(100deg, #c9c4bd 0%, #ddd7cf 30%, #b9c4cf 55%, #d9d1c6 80%, #efe9e0 100%); }

  .cta-box { position: absolute; left: 891px; top: 634px; width: 243px; height: 140px; background: var(--wine); color: #fff; padding: 15px 12px; }
  .cta-box h2 { font-family: "Roboto", sans-serif; font-weight: 700; font-size: 16.5px; line-height: 19.5px; margin-bottom: 10px; }
  .cta-box p { font-family: "Roboto", sans-serif; font-weight: 300; font-size: 12.5px; line-height: 14.5px; }
</style>
</head>
<body>

<section class="page page--left">
  <div class="running-head" style="left:36px">KUNSTFEHLER</div>
  <div class="running-bar" style="left:127px"></div>
  <h1 class="page-title" style="left:36px">ARZTFEHLER KÖNNEN PASSIEREN</h1>

  <blockquote class="lead-quote">
    <p>Aber wie kann man seine erlittenen Schmerzen zumindest durch einen Geldanspruch ausgleichen lassen? Wer übernimmt dafür das Risko?</p>
  </blockquote>

  <div class="column" style="left:36px; top:178px; width:258px;">
    <p>Die Leistung unsere Ärzteschaft in Österreich ist weltweit anerkannt, angesehen und in vielen Bereichen richtungsweisend. Wir können auf deren Leistungen stolz sein, sie leisten oft fast Unmögliches!</p>
    <p>Leider trifft dies jedoch nicht auf alle Ärzte zu. Es häufen sich die Pressemeldungen über fehlerhafte Diagnosen (auch in einfachen Fällen), Komplikationen bei Routineeingriffen oder auch fatalen Fehlleistungen wie z.B. die Amputation falsche Gliedmaßen. <span class="accent-strong">Meist erleiden die Patienten neben körperlichen auch massive psychische Folgeschäden wie z.B. Depressionen.</span></p>
    <p>Manchmal sind dies tragische Einzelfälle, leider jedoch nicht immer.</p>
    <p>Ärzte sind Götter in Weiß. Ein altbekannter Spruch. Deren Wort ist Macht, welches niemand – schon gar nicht der eigene Patient – anzweifeln sollte. Diese Machtstellung nutzen leider machen Ärzte zur Vertuschung ihrer Fehlleistungen aus und argumentieren in die Richtung, allfällige negative Folgen einer Operation oder Behandlung seien eben passiert, einfach „Pech“ und daher zu akzeptieren.</p>
    <p>Eine Klageführung gegen Ärzte ist in der Praxis schwierig und teuer, Rechtsschutzversicherungen sind meist nicht vorhan-</p>
  </div>

  <div class="column" style="left:306px; top:178px; width:258px;">
    <p>den oder lehnen eine Deckung in der erforderlichen Höhe ab.</p>
    <p><span class="accent-strong">Genau hier helfen wir Ihnen weiter! Wir übernehmen Ihr gesamtes Prozessrisiko!</span> Wir empfehlen Ihnen nach einer ersten Analyse Ihres Falles einen spezialisierten Rechtsanwalt, der mit Ihnen Ihren Fall bespricht und sodann Ihren Arzt oder das Spital mit Ihrer Forderung (meistens Schmerzensgeld) konfrontiert.</p>
    <p>Für die Tragung dieses Risikos (die Prozesskosten können je nach Streitwert zigtausende Euros betragen, vor allem die Gutachterkosten sind enorm) vereinbaren Sie mit uns eine Erfolgsbeteiligung.</p>
    <p>Wenn wir für Sie also nichts „erreichen“ hat es Sie nichts gekostet und wir tragen sämtliche Kosten. „Wir sitzen somit in einem Boot“ – und begleiten Sie vertrauensvoll in Ihrer schwierigen Situation.</p>
    <p>Stöbern Sie ein bisschen auf der Homepage, laden Sie dann Ihren Fall hoch, die meisten Erfolge werden mit Fällen erzielt, wenn die Erinnerungen noch sehr frisch sind!</p>
    <p class="accent-strong">Wir helfen Ihnen ehrlich, kompetent und schnell!</p>
    <p class="signature">Ihr Team von Aurelo Prozessfinanzierung</p>
  </div>

  <div class="photo" role="img" aria-label="Foto: verzweifelter Mann sitzt vornübergebeugt auf einem Sofa, die Hände am Kopf"></div>
</section>

<section class="page page--right">
  <div class="running-bar" style="left:36px"></div>
  <div class="running-head" style="left:506px">DAS THEMA</div>
  <h1 class="page-title" style="left:36px">WAS IST EIN ÄRZTLICHER KUNSTFEHLER?</h1>

  <div class="column" style="left:36px; top:113px; width:243px;">
    <h3>WAS IST EIN ÄRZTLICHER KUNSTFEHLER?</h3>
    <p>Dies ist eigentlich ein umgangssprachlicher Ausdruck. Juristisch spricht man von sogenannten <span class="accent">„Behandlungsfehlern“</span>. Diese liegen vor, wenn eine medizinische Behandlung nicht nach den zum Zeitpunkt der Behandlung bestehenden, allgemein anerkannten fachlichen Standards erfolgt.</p>
    <p>Es ist egal, ob dieser Fehler aus einen <span class="accent">aktiven Tun</span> (z.B. falsche Operation) oder einem bloßen <span class="accent">Unterlassen</span> (mangelnde Aufklärung über Risken) resultierte.</p>
    <h3>WAS KANN DER VERLETZTE PATIENT FORDERN?</h3>
    <p>Erleidet nun ein Patient durch ein pflichtwidriges Verhalten eines Arztes (Behandlungsfehler) einen Schaden (z.B. Schmerzen), so kann der Verletzte dafür einen Geldbetrag fordern.</p>
    <p>Man kann diese Forderungen wie folgt einteilen:</p>
    <ul class="bullets bullets--indented">
      <li><span class="accent">Schmerzengeld für erlittene Schmerzen.</span> Diese werden gemäß Judikatur in schwere, mittlere und leichte Schmerzen eingeteilt. Multipliziert mit der Dauer dieser Schmerzen ergibt sich der Schmerzengeldanspruch.</li>
      <li>In letzter Zeit kann in Ausnahmefällen auch ein Anspruch für erlittene <span class="accent">seelische Schmerzen</span> zuerkannt werden (z.B.: Trauerschmerzengeld oder Schockschadenansprüche).</li>
      <li>Sind nach dem Ende der Schmerzperiode <span class="accent">weitere Behandlungen</span> notwendig sind auch diese Kosten zu ersetzen (physikalische Therapien, Kuraufenthalte, Massagen, Medikamente, Fahrtkosten)</li>
      <li>Ist bis zur Genesung eine <span class="accent">Heimhilfe oder eine weitere Betreuung</span> notwendig sind auch diese Kosten zu ersetzen.</li>
      <li>Sollte der <span class="accent">Umbau der Wohnung</span> notwenig sein (der Patient ist nach dem Behandlungsfehler querschnittsgelähmt), sind auch die Umbaukosten der Wohnung zu ersetzen.</li>
      <li>Bleibt eine bleibende störende Narbe kann dem Patienten eine <span class="accent">Verunstaltungsentschädigung</span> zugesprochen werden.</li>
      <li>Schließlich trifft den Arzt bzw., das Spital auch eine Haftung für alle weiteren <span class="accent">Folgeschäden</span>.</li>
    </ul>
    <h3>WARUM IST EINE ANSPRUCHSVERFOLGUNG IN DER PRAXIS SO SCHWIERIG?</h3>
    <p>Die Antwort liegt auf der Hand. Der „kleine Patient“ steht meist einem ganzen Spital oder einem erfahrenen Arzt gegenüber. Das Spital aber auch der behandelnde Arzt ist immer anwaltlich gut vertreten, eine Schuld wird fast immer abgestritten. <span class="accent">Rechtsschutzversicherungen</span> sind meist nicht vorhanden oder lehnen eine Deckung ab.</p>
  </div>

  <div class="column" style="left:291px; top:113px; width:243px;">
    <p>Das Spital oder der behandelnde Arzt spielen außerdem oft auf Zeit und die <span class="accent">drohende Verjährung</span> (3 Jahre) sitzt den Patienten im Nacken.</p>
    <p>Dem verletzten Patienten bleibt sodann nur mehr die Möglichkeit selbst den Gerichtsweg zu beschreiten, dies ist jedoch mit einem enormen Kostenrisiko verbunden.</p>
    <p>Da die Streitwerte oft hoch sind besteht ein <span class="accent">enormes Prozesskostenrisiko</span> und man ist abhängig von medizinischen Gutachten, deren Ausgang meist nicht vorhersehbar ist.</p>
    <h3>DOCH DAMIT IST NUN SCHLUSS!</h3>
    <p>Wir helfen Ihnen in dieser Situation schnell und unbürokratisch weiter. Wir <span class="accent">übernehmen sämtliche anfallenden Kosten</span>:</p>
    <ul class="bullets">
      <li>Anwaltliches Erstgespräch und Folgegespräche</li>
      <li>Aufforderungsschreiben gegen die Versicherung</li>
      <li>Verhandlungen mit der Versicherung</li>
      <li>Klage gegen die Versicherung</li>
      <li>Kosten von Gutachten</li>
      <li>Kosten der Gerichtsverhandlungen</li>
      <li>Kosten von Berufungen und Revisionen</li>
    </ul>
    <p>Als Gegenleistung dafür teilen Sie mit uns den erstrittenen Betrag. Sie haben daher keinerlei Risiko.</p>
    <p>Sobald Sie Ihre Daten hochgeladen haben erfolgt eine erste Durchsicht Ihrer Akten. Sollte alles vollständig und der Akt erfolgversprechend sein schlagen wir Ihnen einen unserer <span class="accent">spezialisierten Rechtsanwälte</span> vor. Diese erörtern mit Ihnen Ihren Fall und leiten die erforderlichen Schritte ein.</p>
    <p>Gerne helfen wir Ihnen, Sie haben nun einen <span class="accent">starken Partner</span>, der Ihnen eine <span class="accent">Verhandlung gegen die meist übermächtigen Spitäler oder Ärzte auf Augenhöhe ermöglicht!</span></p>
  </div>
</section>

<aside class="cta-box">
  <h2>WIE GEHT ES FÜR SIE<br>NUN WEITER?</h2>
  <p>Füllen Sie das Einlegeblatt aus und senden Sie dieses an uns zurück oder schicken Sie uns Ihre Unterlagen über www.heilirrtum-hilfe.at</p>
</aside>

</body>
</html>
```